Website for software company "velora"

We need a website for our software company/startup named "velora". We are developing several products (currently 3 standard-software products) which are all in different sectors, but all our products are available for Laptops/PC/Mobile Phones/Tablets, ... We do also create custom software and support our customers with consulting to optimize their processes.
We already have a Logo which you can find in the attached files.
We are a young team of 4 members (two founders and 2 employees).

To get an idea of our products -> the first one is a planning software for healthcare organizations (eg. BlueHaven, firebrigade, pharmacy), the second one is a booking software for sport clubs and the third one is a competition software for sports hunting. You see very diverse. Include or ignore this info of our products as you like.

The design has to be a bootstrap 4 (or higher) design. We have licenced FontAwesome as iconset. Responsive design should come without saying.

• Starting page, product pages, news section, contact, team, services

```html
<!DOCTYPE html>
<html lang="en">
<head>
<meta charset="utf-8">
<title>velora – Inner Pages</title>
<link rel="stylesheet" href="https://fonts.googleapis.com/css2?family=Montserrat:wght@400;500;600;700;800&family=Nunito+Sans:wght@400;600&display=swap">
<style>
:root{
  --board:#8e9ba7;
  --orange:#f07c1e;
  --dark:#2d333d;
  --ink:#1f2329;
  --muted:#6b7280;
  --hero:#f3f4f6;
  --white:#ffffff;
}
*{margin:0;padding:0;box-sizing:border-box}
html,body{width:1200px;height:779px;overflow:hidden;background:var(--board)}
body{position:relative;font-family:"Nunito Sans",Arial,sans-serif;color:var(--ink)}
.board-title{position:absolute;top:34px;left:0;width:1200px;text-align:center;font-family:"Montserrat",Arial,sans-serif;font-weight:700;font-size:52px;letter-spacing:1px;color:var(--white)}
.page{position:absolute;top:146px;width:293px;height:559px;background:var(--white);overflow:hidden;box-shadow:0 3px 10px rgba(0,0,0,.18)}
.page *{position:absolute}
.page b,.page em,.page .brand-mark,.page .nav-links span,.page .dropdown p,.page .col-list p{position:static}
.section-layer{left:0;top:0;width:100%;height:100%}
.topbar{left:0;top:0;width:100%;height:5px;background:var(--dark)}
.topbar .social{top:1px;width:3px;height:3px;background:#cfd4da}
.topbar .info{top:0;font-size:2.4px;line-height:5px;color:#e5e7eb;white-space:nowrap}
.navbar{left:0;top:5px;width:100%;height:11px;background:var(--white)}
.brand{font-family:"Montserrat",sans-serif;font-weight:700;color:var(--dark);white-space:nowrap}
.navbar .brand{left:32px;top:1px;font-size:7.5px;line-height:9px}
.brand-mark{display:inline-block;width:4px;height:4px;background:var(--orange);margin-right:1.5px;vertical-align:middle}
.nav-links{left:144px;top:3px;width:119px;display:flex;justify-content:space-between;font-family:"Montserrat",sans-serif;font-size:2.6px;line-height:4px;color:var(--ink);white-space:nowrap}
.nav-links .active{color:var(--orange)}
.dropdown{left:185px;top:13px;width:38px;height:21px;background:var(--dark);padding:2px 3px;z-index:2}
.dropdown p{font-size:2.4px;line-height:5px;color:#e5e7eb;white-space:nowrap}
.dropdown p.current{color:var(--orange)}
.hero{left:0;top:16px;width:100%;height:65px;background:var(--hero)}
.hero-title{left:0;top:14px;width:100%;text-align:center;font-family:"Montserrat",sans-serif;font-weight:500;font-size:8.5px;line-height:10px;color:var(--dark);white-space:nowrap}
.hero-title b{font-weight:500;color:var(--orange)}
.hero-text{left:70px;top:27px;width:153px;text-align:center;font-size:3px;line-height:4.5px;color:var(--ink)}
.btn{top:41px;height:8px;font-family:"Montserrat",sans-serif;font-size:2.4px;line-height:8px;text-align:center;color:var(--white);font-weight:600;white-space:nowrap}
.btn-primary{left:119px;width:27px;background:var(--orange)}
.btn-dark{left:148px;width:27px;background:var(--dark)}
.shot{border-radius:2px}
.devices{left:50px;top:91px;width:193px;height:91px}
.eyebrow{font-family:"Montserrat",sans-serif;font-size:4.5px;line-height:6px;color:var(--ink);white-space:nowrap}
.heading{font-family:"Montserrat",sans-serif;font-weight:600;font-size:8.3px;line-height:10px;color:var(--ink);white-space:nowrap}
.body-text{font-size:2.8px;line-height:4.4px;color:var(--ink)}
.intro .eyebrow{left:0;top:194px;width:100%;text-align:center}
.intro .heading{left:0;top:200px;width:100%;text-align:center}
.intro .body-text{left:32px;top:214px;width:229px;text-align:center}
.feature-icon{width:10px;height:10px;border-radius:1px}
.feature-icon.orange{background:var(--orange)}
.feature-icon.dark{background:var(--dark)}
.feature-icon svg{left:2px;top:2px}
.feature-name{font-family:"Montserrat",sans-serif;font-weight:600;font-size:3.8px;line-height:5px;color:var(--ink);white-space:nowrap}
.feature-desc{font-size:2.5px;line-height:3.8px;color:var(--muted);width:47px}
.features .eyebrow{left:32px;top:274px}
.features .heading{left:32px;top:281px}
.features .body-text{left:32px;top:293px;width:114px}
.tablet{left:173px;top:247px;width:90px;height:116px;border-radius:5px}
.efficiency .eyebrow{left:137px;top:390px}
.efficiency .heading{left:137px;top:397px}
.efficiency .body-text{left:137px;top:410px;width:113px}
.dashboard{left:32px;top:391px;width:98px;height:71px}
.footer{left:0;top:474px;width:100%;height:85px;background:var(--dark)}
.footer .brand{left:32px;top:10px;font-size:12px;line-height:14px;color:var(--white)}
.footer .brand-mark{width:6px;height:6px}
.footer-about{left:32px;top:28px;width:58px;font-size:2.6px;line-height:4px;color:#cbd0d6}
.footer-social{top:49px;width:7px;height:7px;background:var(--white)}
.footer-social.first{background:#2f5bd3}
.col-title{top:11px;font-family:"Montserrat",sans-serif;font-size:3.6px;line-height:5px;color:var(--orange);white-space:nowrap}
.col-list{top:18px;width:50px;font-size:2.5px;line-height:6.5px;color:#cbd0d6;white-space:nowrap}
.contact-row{left:208px;width:70px;height:8px}
.contact-row i{left:0;top:0;width:6px;height:6px;border-radius:50%;background:var(--white)}
.contact-row i svg{left:1.2px;top:1.2px}
.contact-row span{left:8px;top:0;font-size:2.5px;line-height:3.6px;color:#e5e7eb;width:60px}
.copyright{left:0;top:71px;width:100%;text-align:center;font-size:2.4px;line-height:4px;color:#cbd0d6}
.copyright em{font-style:normal;color:var(--orange)}
</style>
</head>
<body>

<h1 class="board-title">INNER PAGE</h1>

<!-- ===== Healthcare Organizations ===== -->
<section class="page" style="left:96px">
  <div class="topbar">
    <i class="social" style="left:32px"></i><i class="social" style="left:38px"></i><i class="social" style="left:44px"></i>
    <span class="info" style="left:204px">+43 (0) 555 0142</span>
    <span class="info" style="left:239px">hello@velora.example</span>
  </div>
  <header class="navbar">
    <div class="brand"><span class="brand-mark"></span>velora</div>
    <nav class="nav-links"><span>HOME</span><span>SERVICES</span><span class="active">PRODUCTS ˅</span><span>NEWS</span><span>TEAM</span><span>CONTACT US</span></nav>
  </header>
  <div class="hero">
    <h2 class="hero-title"><b>HEALTHCARE</b> ORGANIZATIONS</h2>
    <p class="hero-text">Sed ut perspiciatis unde omnis iste natus error sit voluptatem accusantium doloremque laudantium, totam rem aperiam, eaque ipsa quae ab illo inventore veritatis et quasi</p>
    <span class="btn btn-primary">START FREE TRIAL</span>
    <span class="btn btn-dark">CONTACT US</span>
  </div>
  <div class="dropdown"><p class="current">Healthcare Organizations</p><p>Sport Clubs</p><p>Sports Hunting</p></div>
  <div class="shot devices" role="img" aria-label="Healthcare planning dashboard shown on desktop, laptop and phone" style="background:linear-gradient(180deg,#fff 0%,#eef1f6 30%,#d9e2ee 70%,#fff 100%)"></div>
  <div class="section-layer intro">
    <p class="eyebrow">Excepteur sint</p>
    <h3 class="heading">Occaecat Cupidatat Proident</h3>
    <p class="body-text">Sed ut perspiciatis unde omnis iste natus error sit voluptatem accusantium doloremque laudantium, totam rem aperiam, eaque ipsa quae ab illo inventore veritatis et quasi architecto beatae vitae dicta sunt explicabo. Nemo enim ipsam voluptatem quia voluptas sit aspernatur aut odit aut fugit, sed quia consequuntur magni dolores eos qui ratione voluptatem sequi nesciunt.</p>
  </div>
  <div class="section-layer features">
    <p class="eyebrow">Browse our</p>
    <h3 class="heading">World Class Features</h3>
    <p class="body-text">Sed ut perspiciatis unde omnis iste natus error sit voluptatem accusantium doloremque laudantium, totam rem aperiam, eaque ipsa quae ab illo inventore veritatis et quasi architecto beatae vitae dicta sunt explicabo. Nemo enim ipsam voluptatem quia voluptas sit aspe...</p>
    <span class="feature-icon orange" style="left:32px;top:324px"><svg width="6" height="6" viewBox="0 0 6 6"><rect x=".5" y=".8" width="5" height="4.4" fill="none" stroke="#fff" stroke-width=".6"/></svg></span>
    <span class="feature-name" style="left:45px;top:323px">Customer Analysis</span>
    <span class="feature-desc" style="left:45px;top:329px">Objectively productize exceptional via customized.</span>
    <span class="feature-icon dark" style="left:99px;top:324px"><svg width="6" height="6" viewBox="0 0 6 6"><rect x=".5" y=".5" width="5" height="5" fill="none" stroke="#fff" stroke-width=".6"/></svg></span>
    <span class="feature-name" style="left:112px;top:323px">Real Time Metrics</span>
    <span class="feature-desc" style="left:112px;top:329px">Objectively productize exceptional via customized.</span>
    <div class="shot tablet" role="img" aria-label="Project metrics dashboard on a tablet" style="background:linear-gradient(160deg,#2a2f38 0%,#1b2a3a 50%,#1f4e63 100%)"></div>
  </div>
  <div class="section-layer efficiency">
    <div class="shot dashboard" role="img" aria-label="Teal finance dashboard screen" style="background:linear-gradient(135deg,#1aa38a 0%,#15806f 55%,#0f5a54 100%)"></div>
    <p class="eyebrow">Measure your</p>
    <h3 class="heading">Efficiency for Business</h3>
    <p class="body-text">Sed ut perspiciatis unde omnis iste natus error sit voluptatem accusantium doloremque laudantium, totam rem aperiam, eaque ipsa quae ab illo inventore veritatis et quasi architecto beatae vitae dicta sunt explicabo. Nemo enim ipsam voluptatem quia voluptas sit aspe...</p>
    <span class="feature-icon orange" style="left:137px;top:441px"><svg width="6" height="6" viewBox="0 0 6 6"><rect x=".5" y=".8" width="5" height="4.4" fill="none" stroke="#fff" stroke-width=".6"/></svg></span>
    <span class="feature-name" style="left:150px;top:440px">Finance Models</span>
    <span class="feature-desc" style="left:150px;top:446px">Objectively productize exceptional via customized.</span>
    <span class="feature-icon dark" style="left:204px;top:441px"><svg width="6" height="6" viewBox="0 0 6 6"><rect x=".5" y=".5" width="5" height="5" fill="none" stroke="#fff" stroke-width=".6"/></svg></span>
    <span class="feature-name" style="left:217px;top:440px">Daily Consultancy</span>
    <span class="feature-desc" style="left:217px;top:446px">Objectively productize exceptional via customized.</span>
  </div>
  <footer class="footer">
    <div class="brand"><span class="brand-mark"></span>velora</div>
    <p class="footer-about">At vero eos et accusamus et iusto odio dignissimos ducimus qui blanditiis praesentium</p>
    <i class="footer-social first" style="left:32px"></i><i class="footer-social" style="left:41px"></i><i class="footer-social" style="left:50px"></i>
    <h4 class="col-title" style="left:108px">Sitemap</h4>
    <div class="col-list" style="left:108px"><p>› Home</p><p>› Services</p><p>› Products</p><p>› News</p><p>› Team</p><p>› Contact Us</p></div>
    <h4 class="col-title" style="left:150px">Products</h4>
    <div class="col-list" style="left:150px"><p>› Healthcare Organizations</p><p>› Sport Clubs</p><p>› Sports Hunting</p></div>
    <h4 class="col-title" style="left:208px">Contact Us</h4>
    <div class="contact-row" style="top:21px"><i><svg width="3.6" height="3.6" viewBox="0 0 6 6"><path d="M3 .5a2 2 0 0 1 2 2c0 1.5-2 3-2 3s-2-1.5-2-3a2 2 0 0 1 2-2z" fill="#2d333d"/></svg></i><span>15/K Lorem ipsum dolor sit amet Brookfield 25L USA</span></div>
    <div class="contact-row" style="top:35px"><i><svg width="3.6" height="3.6" viewBox="0 0 6 6"><path d="M1 1l1.3-.3.8 1.5-.8.6a3.5 3.5 0 0 0 1.9 1.9l.6-.8 1.5.8L6 5.7C3 6 0 3 .3 0z" fill="#2d333d"/></svg></i><span>+43 (0) 555 0142</span></div>
    <div class="contact-row" style="top:47px"><i><svg width="3.6" height="3.6" viewBox="0 0 6 6"><rect x=".5" y="1.2" width="5" height="3.6" fill="#2d333d"/></svg></i><span>hello@velora.example</span></div>
    <p class="copyright">Copyright © 2022 <em>velora</em>. All Rights Reserved.</p>
  </footer>
</section>

<!-- ===== Sport Club ===== -->
<section class="page" style="left:453px">
  <div class="topbar">
    <i class="social" style="left:32px"></i><i class="social" style="left:38px"></i><i class="social" style="left:44px"></i>
    <span class="info" style="left:204px">+43 (0) 555 0142</span>
    <span class="info" style="left:239px">hello@velora.example</span>
  </div>
  <header class="navbar">
    <div class="brand"><span class="brand-mark"></span>velora</div>
    <nav class="nav-links"><span>HOME</span><span>SERVICES</span><span class="active">PRODUCTS ˅</span><span>NEWS</span><span>TEAM</span><span>CONTACT US</span></nav>
  </header>
  <div class="hero">
    <h2 class="hero-title"><b>SPORT</b> CLUB</h2>
    <p class="hero-text">Sed ut perspiciatis unde omnis iste natus error sit voluptatem accusantium doloremque laudantium, totam rem aperiam, eaque ipsa quae ab illo inventore veritatis et quasi</p>
    <span class="btn btn-primary">START FREE TRIAL</span>
    <span class="btn btn-dark">CONTACT US</span>
  </div>
  <div class="dropdown"><p>Healthcare Organizations</p><p class="current">Sport Clubs</p><p>Sports Hunting</p></div>
  <div class="shot devices" role="img" aria-label="Sport club booking app shown on desktop, laptop and phone" style="background:linear-gradient(180deg,#fff 0%,#eef3f1 30%,#d6e6e0 70%,#fff 100%)"></div>
  <div class="section-layer intro">
    <p class="eyebrow">Excepteur sint</p>
    <h3 class="heading">Occaecat Cupidatat Proident</h3>
    <p class="body-text">Sed ut perspiciatis unde omnis iste natus error sit voluptatem accusantium doloremque laudantium, totam rem aperiam, eaque ipsa quae ab illo inventore veritatis et quasi architecto beatae vitae dicta sunt explicabo. Nemo enim ipsam voluptatem quia voluptas sit aspernatur aut odit aut fugit, sed quia consequuntur magni dolores eos qui ratione voluptatem sequi nesciunt.</p>
  </div>
  <div class="section-layer features">
    <p class="eyebrow">Browse our</p>
    <h3 class="heading">World Class Features</h3>
    <p class="body-text">Sed ut perspiciatis unde omnis iste natus error sit voluptatem accusantium doloremque laudantium, totam rem aperiam, eaque ipsa quae ab illo inventore veritatis et quasi architecto beatae vitae dicta sunt explicabo. Nemo enim ipsam voluptatem quia voluptas sit aspe...</p>
    <span class="feature-icon orange" style="left:32px;top:324px"><svg width="6" height="6" viewBox="0 0 6 6"><rect x=".5" y=".8" width="5" height="4.4" fill="none" stroke="#fff" stroke-width=".6"/></svg></span>
    <span class="feature-name" style="left:45px;top:323px">Customer Analysis</span>
    <span class="feature-desc" style="left:45px;top:329px">Objectively productize exceptional via customized.</span>
    <span class="feature-icon dark" style="left:99px;top:324px"><svg width="6" height="6" viewBox="0 0 6 6"><rect x=".5" y=".5" width="5" height="5" fill="none" stroke="#fff" stroke-width=".6"/></svg></span>
    <span class="feature-name" style="left:112px;top:323px">Real Time Metrics</span>
    <span class="feature-desc" style="left:112px;top:329px">Objectively productize exceptional via customized.</span>
    <div class="shot tablet" role="img" aria-label="Player statistics screen on a tablet" style="background:linear-gradient(160deg,#2b2f36 0%,#23272e 50%,#3a2a26 100%)"></div>
  </div>
  <div class="section-layer efficiency">
    <div class="shot dashboard" role="img" aria-label="Green fitness dashboard screen" style="background:linear-gradient(135deg,#4cc37a 0%,#e9f4ee 35%,#f6f8f7 100%)"></div>
    <p class="eyebrow">Measure your</p>
    <h3 class="heading">Efficiency for Business</h3>
    <p class="body-text">Sed ut perspiciatis unde omnis iste natus error sit voluptatem accusantium doloremque laudantium, totam rem aperiam, eaque ipsa quae ab illo inventore veritatis et quasi architecto beatae vitae dicta sunt explicabo. Nemo enim ipsam voluptatem quia voluptas sit aspe...</p>
    <span class="feature-icon orange" style="left:137px;top:441px"><svg width="6" height="6" viewBox="0 0 6 6"><rect x=".5" y=".8" width="5" height="4.4" fill="none" stroke="#fff" stroke-width=".6"/></svg></span>
    <span class="feature-name" style="left:150px;top:440px">Finance Models</span>
    <span class="feature-desc" style="left:150px;top:446px">Objectively productize exceptional via customized.</span>
    <span class="feature-icon dark" style="left:204px;top:441px"><svg width="6" height="6" viewBox="0 0 6 6"><rect x=".5" y=".5" width="5" height="5" fill="none" stroke="#fff" stroke-width=".6"/></svg></span>
    <span class="feature-name" style="left:217px;top:440px">Daily Consultancy</span>
    <span class="feature-desc" style="left:217px;top:446px">Objectively productize exceptional via customized.</span>
  </div>
  <footer class="footer">
    <div class="brand"><span class="brand-mark"></span>velora</div>
    <p class="footer-about">At vero eos et accusamus et iusto odio dignissimos ducimus qui blanditiis praesentium</p>
    <i class="footer-social first" style="left:32px"></i><i class="footer-social" style="left:41px"></i><i class="footer-social" style="left:50px"></i>
    <h4 class="col-title" style="left:108px">Sitemap</h4>
    <div class="col-list" style="left:108px"><p>› Home</p><p>› Services</p><p>› Products</p><p>› News</p><p>› Team</p><p>› Contact Us</p></div>
    <h4 class="col-title" style="left:150px">Products</h4>
    <div class="col-list" style="left:150px"><p>› Healthcare Organizations</p><p>› Sport Clubs</p><p>› Sports Hunting</p></div>
    <h4 class="col-title" style="left:208px">Contact Us</h4>
    <div class="contact-row" style="top:21px"><i><svg width="3.6" height="3.6" viewBox="0 0 6 6"><path d="M3 .5a2 2 0 0 1 2 2c0 1.5-2 3-2 3s-2-1.5-2-3a2 2 0 0 1 2-2z" fill="#2d333d"/></svg></i><span>15/K Lorem ipsum dolor sit amet Brookfield 25L USA</span></div>
    <div class="contact-row" style="top:35px"><i><svg width="3.6" height="3.6" viewBox="0 0 6 6"><path d="M1 1l1.3-.3.8 1.5-.8.6a3.5 3.5 0 0 0 1.9 1.9l.6-.8 1.5.8L6 5.7C3 6 0 3 .3 0z" fill="#2d333d"/></svg></i><span>+43 (0) 555 0142</span></div>
    <div class="contact-row" style="top:47px"><i><svg width="3.6" height="3.6" viewBox="0 0 6 6"><rect x=".5" y="1.2" width="5" height="3.6" fill="#2d333d"/></svg></i><span>hello@velora.example</span></div>
    <p class="copyright">Copyright © 2022 <em>velora</em>. All Rights Reserved.</p>
  </footer>
</section>

<!-- ===== Sport Hunting ===== -->
<section class="page" style="left:811px">
  <div class="topbar">
    <i class="social" style="left:32px"></i><i class="social" style="left:38px"></i><i class="social" style="left:44px"></i>
    <span class="info" style="left:204px">+43 (0) 555 0142</span>
    <span class="info" style="left:239px">hello@velora.example</span>
  </div>
  <header class="navbar">
    <div class="brand"><span class="brand-mark"></span>velora</div>
    <nav class="nav-links"><span>HOME</span><span>SERVICES</span><span class="active">PRODUCTS ˅</span><span>NEWS</span><span>TEAM</span><span>CONTACT US</span></nav>
  </header>
  <div class="hero">
    <h2 class="hero-title"><b>SPORT</b> HUNTING</h2>
    <p class="hero-text">Sed ut perspiciatis unde omnis iste natus error sit voluptatem accusantium doloremque laudantium, totam rem aperiam, eaque ipsa quae ab illo inventore veritatis et quasi</p>
    <span class="btn btn-primary">START FREE TRIAL</span>
    <span class="btn btn-dark">CONTACT US</span>
  </div>
  <div class="dropdown"><p>Healthcare Organizations</p><p>Sport Clubs</p><p class="current">Sports Hunting</p></div>
  <div class="shot devices" role="img" aria-label="Competition results software shown on desktop, laptop and phone" style="background:linear-gradient(180deg,#fff 0%,#eef2f4 30%,#d7e3ea 70%,#fff 100%)"></div>
  <div class="section-layer intro">
    <p class="eyebrow">Excepteur sint</p>
    <h3 class="heading">Occaecat Cupidatat Proident</h3>
    <p class="body-text">Sed ut perspiciatis unde omnis iste natus error sit voluptatem accusantium doloremque laudantium, totam rem aperiam, eaque ipsa quae ab illo inventore veritatis et quasi architecto beatae vitae dicta sunt explicabo. Nemo enim ipsam voluptatem quia voluptas sit aspernatur aut odit aut fugit, sed quia consequuntur magni dolores eos qui ratione voluptatem sequi nesciunt.</p>
  </div>
  <div class="section-layer features">
    <p class="eyebrow">Browse our</p>
    <h3 class="heading">World Class Features</h3>
    <p class="body-text">Sed ut perspiciatis unde omnis iste natus error sit voluptatem accusantium doloremque laudantium, totam rem aperiam, eaque ipsa quae ab illo inventore veritatis et quasi architecto beatae vitae dicta sunt explicabo. Nemo enim ipsam voluptatem quia voluptas sit aspe...</p>
    <span class="feature-icon orange" style="left:32px;top:324px"><svg width="6" height="6" viewBox="0 0 6 6"><rect x=".5" y=".8" width="5" height="4.4" fill="none" stroke="#fff" stroke-width=".6"/></svg></span>
    <span class="feature-name" style="left:45px;top:323px">Customer Analysis</span>
    <span class="feature-desc" style="left:45px;top:329px">Objectively productize exceptional via customized.</span>
    <span class="feature-icon dark" style="left:99px;top:324px"><svg width="6" height="6" viewBox="0 0 6 6"><rect x=".5" y=".5" width="5" height="5" fill="none" stroke="#fff" stroke-width=".6"/></svg></span>
    <span class="feature-name" style="left:112px;top:323px">Real Time Metrics</span>
    <span class="feature-desc" style="left:112px;top:329px">Objectively productize exceptional via customized.</span>
    <div class="shot tablet" role="img" aria-label="Activity feed screen on a tablet" style="background:linear-gradient(90deg,#2a2f38 0%,#2a2f38 35%,#f4f6f8 36%,#ffffff 100%)"></div>
  </div>
  <div class="section-layer efficiency">
    <div class="shot dashboard" role="img" aria-label="Light statistics dashboard screen" style="background:linear-gradient(135deg,#f7f8fb 0%,#eef1f7 60%,#e4e9f3 100%)"></div>
    <p class="eyebrow">Measure your</p>
    <h3 class="heading">Efficiency for Business</h3>
    <p class="body-text">Sed ut perspiciatis unde omnis iste natus error sit voluptatem accusantium doloremque laudantium, totam rem aperiam, eaque ipsa quae ab illo inventore veritatis et quasi architecto beatae vitae dicta sunt explicabo. Nemo enim ipsam voluptatem quia voluptas sit aspe...</p>
    <span class="feature-icon orange" style="left:137px;top:441px"><svg width="6" height="6" viewBox="0 0 6 6"><rect x=".5" y=".8" width="5" height="4.4" fill="none" stroke="#fff" stroke-width=".6"/></svg></span>
    <span class="feature-name" style="left:150px;top:440px">Finance Models</span>
    <span class="feature-desc" style="left:150px;top:446px">Objectively productize exceptional via customized.</span>
    <span class="feature-icon dark" style="left:204px;top:441px"><svg width="6" height="6" viewBox="0 0 6 6"><rect x=".5" y=".5" width="5" height="5" fill="none" stroke="#fff" stroke-width=".6"/></svg></span>
    <span class="feature-name" style="left:217px;top:440px">Daily Consultancy</span>
    <span class="feature-desc" style="left:217px;top:446px">Objectively productize exceptional via customized.</span>
  </div>
  <footer class="footer">
    <div class="brand"><span class="brand-mark"></span>velora</div>
    <p class="footer-about">At vero eos et accusamus et iusto odio dignissimos ducimus qui blanditiis praesentium</p>
    <i class="footer-social first" style="left:32px"></i><i class="footer-social" style="left:41px"></i><i class="footer-social" style="left:50px"></i>
    <h4 class="col-title" style="left:108px">Sitemap</h4>
    <div class="col-list" style="left:108px"><p>› Home</p><p>› Services</p><p>› Products</p><p>› News</p><p>› Team</p><p>› Contact Us</p></div>
    <h4 class="col-title" style="left:150px">Products</h4>
    <div class="col-list" style="left:150px"><p>› Healthcare Organizations</p><p>› Sport Clubs</p><p>› Sports Hunting</p></div>
    <h4 class="col-title" style="left:208px">Contact Us</h4>
    <div class="contact-row" style="top:21px"><i><svg width="3.6" height="3.6" viewBox="0 0 6 6"><path d="M3 .5a2 2 0 0 1 2 2c0 1.5-2 3-2 3s-2-1.5-2-3a2 2 0 0 1 2-2z" fill="#2d333d"/></svg></i><span>15/K Lorem ipsum dolor sit amet Brookfield 25L USA</span></div>
    <div class="contact-row" style="top:35px"><i><svg width="3.6" height="3.6" viewBox="0 0 6 6"><path d="M1 1l1.3-.3.8 1.5-.8.6a3.5 3.5 0 0 0 1.9 1.9l.6-.8 1.5.8L6 5.7C3 6 0 3 .3 0z" fill="#2d333d"/></svg></i><span>+43 (0) 555 0142</span></div>
    <div class="contact-row" style="top:47px"><i><svg width="3.6" height="3.6" viewBox="0 0 6 6"><rect x=".5" y="1.2" width="5" height="3.6" fill="#2d333d"/></svg></i><span>hello@velora.example</span></div>
    <p class="copyright">Copyright © 2022 <em>velora</em>. All Rights Reserved.</p>
  </footer>
</section>

</body>
</html>
```